Bry7Legal Letterhead

Need a new letterhead for my law firm.
IDENTIFYING INFORMATION BELOW:
Anselmo R Quintara III
Attorney at Law
Address: 2847 Larkspur Blvd, Ste 300, Dallas, TX 75204
Phone: 877-482-6017
Fax: 469-738-1452
Email: bry@bry7legal.example
Website: www.bry7legal.example

Colors
0054AA
0677BA
7BADD7
CADEEF
E8F1F8

Requirements
Must have
• Logo needs to be on the letterhead, along with identifying information which is included in the project description.

```html
<!DOCTYPE html>
<html lang="en">
<head>
<meta charset="utf-8">
<title>Bry7Legal Letterhead</title>
<link rel="stylesheet" href="https://fonts.googleapis.com/css2?family=Lato:wght@700;900&family=Roboto+Condensed:wght@400&display=swap">
<style>
  :root {
    --backdrop: #3c3c3e;
    --paper: #f9f9f9;
    --paper-tint: #f1f1f1;
    --ink: #0b0b0c;
    --rule: #b5b5b5;
    --text: #1a1a1a;
    --white: #ffffff;
    --blue-dark: #0054aa;
    --blue-mid: #0677ba;
    --blue-light: #1aa3dc;
  }
  * { margin: 0; padding: 0; box-sizing: border-box; }
  html, body { width: 849px; height: 1200px; overflow: hidden; background: var(--backdrop); }
  .canvas { position: relative; width: 849px; height: 1200px; }
  .letterhead {
    position: absolute; left: 68px; top: 95px; width: 713px; height: 1009px;
    background: var(--paper); overflow: hidden;
  }
  .pattern-field {
    position: absolute; inset: 0; background: var(--paper);
  }
  .header-art { position: absolute; left: 0; top: 0; }
  .brand-name {
    position: absolute; left: 208px; width: 330px; top: 28px; text-align: center;
    font-family: "Lato", sans-serif; font-weight: 900; font-size: 33px;
    letter-spacing: 1px; color: var(--white);
  }
  .attorney {
    position: absolute; left: 40px; top: 106px;
    font-family: "Lato", sans-serif; font-weight: 900; font-size: 18.5px;
    line-height: 19px; color: var(--ink); text-transform: uppercase;
  }
  .contact-list {
    position: absolute; left: 508px; top: 66px; list-style: none;
    font-family: "Roboto Condensed", sans-serif; font-size: 13.5px; color: var(--text);
  }
  .contact-item { display: flex; align-items: flex-start; height: 19px; line-height: 19px; }
  .contact-item.address { height: 38px; }
  .contact-icon { width: 15px; height: 15px; margin-top: 2px; flex: none; }
  .contact-sep { margin: 0 5px 0 6px; }
  .header-rule {
    position: absolute; left: 27px; top: 194px; width: 658px; height: 1px; background: var(--rule);
  }
  .letter-date {
    position: absolute; left: 563px; top: 228px;
    font-family: "Roboto Condensed", sans-serif; font-size: 14px; color: var(--text);
  }
  .center-mark {
    position: absolute; left: 161px; top: 464px; width: 386px; height: 101px;
    background: var(--paper-tint); display: flex; align-items: center; justify-content: center;
    font-family: "Lato", sans-serif; font-weight: 900; font-size: 54px; color: #f9f9f9;
    letter-spacing: 2px;
  }
  .footer-band { position: absolute; left: 0; bottom: 0; }
</style>
</head>
<body>
<div class="canvas">
  <section class="letterhead">
    <div class="pattern-field" role="img" aria-label="Faint repeating background pattern of the firm name"></div>

    <svg class="header-art" width="713" height="160" viewBox="0 0 713 160">
      <polygon points="140,0 530,0 399,156" fill="var(--ink)"/>
    </svg>
    <div class="brand-name">Bry7Legal</div>

    <h1 class="attorney">Anselmo R Quintara III<br>Attorney at Law</h1>

    <ul class="contact-list">
      <li class="contact-item address">
        <svg class="contact-icon" viewBox="0 0 16 16"><circle cx="8" cy="8" r="8" fill="var(--ink)"/><path d="M8 3.2a3 3 0 0 0-3 3c0 2.3 3 6 3 6s3-3.7 3-6a3 3 0 0 0-3-3z" fill="var(--white)"/><circle cx="8" cy="6.2" r="1.1" fill="var(--ink)"/></svg>
        <span class="contact-sep">|</span>
        <span>2847 Larkspur Blvd,<br>Ste 300, Dallas, TX 75204</span>
      </li>
      <li class="contact-item">
        <svg class="contact-icon" viewBox="0 0 16 16"><circle cx="8" cy="8" r="8" fill="var(--ink)"/><path d="M5 3.8l1.4-.4 1 2.2-.9.8c.5 1.1 1.3 1.9 2.3 2.4l.8-.9 2.2 1-.4 1.4c-3.3.3-6.6-3-6.4-6.5z" fill="var(--white)"/></svg>
        <span class="contact-sep">|</span><span>Phone: 877-482-6017</span>
      </li>
      <li class="contact-item">
        <svg class="contact-icon" viewBox="0 0 16 16"><circle cx="8" cy="8" r="8" fill="var(--ink)"/><rect x="4" y="6" width="8" height="6" rx="1" fill="var(--white)"/><rect x="5.5" y="3.5" width="5" height="3" fill="var(--white)"/><rect x="6" y="8" width="4" height="1" fill="var(--ink)"/></svg>
        <span class="contact-sep">|</span><span>Fax: 469-738-1452</span>
      </li>
      <li class="contact-item">
        <svg class="contact-icon" viewBox="0 0 16 16"><circle cx="8" cy="8" r="8" fill="var(--ink)"/><rect x="3.8" y="5" width="8.4" height="6" rx=".6" fill="var(--white)"/><path d="M3.8 5.3L8 8.3l4.2-3" stroke="var(--ink)" stroke-width=".9" fill="none"/></svg>
        <span class="contact-sep">|</span><span>Email: bry@bry7legal.example</span>
      </li>
      <li class="contact-item">
        <svg class="contact-icon" viewBox="0 0 16 16"><circle cx="8" cy="8" r="8" fill="var(--ink)"/><g stroke="var(--white)" stroke-width=".9" fill="none"><circle cx="8" cy="8" r="4.3"/><ellipse cx="8" cy="8" rx="1.8" ry="4.3"/><path d="M3.7 8h8.6M4.4 5.8h7.2M4.4 10.2h7.2"/></g></svg>
        <span class="contact-sep">|</span><span>Website: www.bry7legal.example</span>
      </li>
    </ul>

    <div class="header-rule"></div>
    <p class="letter-date">Date: 00 /00/0000</p>

    <div class="center-mark">Bry7Legal</div>

    <svg class="footer-band" width="713" height="8" viewBox="0 0 713 8">
      <defs>
        <linearGradient id="band-blue" x1="0" x2="1">
          <stop offset="0" stop-color="var(--blue-light)"/>
          <stop offset="0.6" stop-color="var(--blue-mid)"/>
          <stop offset="1" stop-color="var(--blue-dark)"/>
        </linearGradient>
      </defs>
      <rect width="713" height="8" fill="var(--ink)"/>
      <polygon points="458,0 713,0 713,8 476,8" fill="url(#band-blue)"/>
    </svg>
  </section>
</div>
</body>
</html>
```